Bookcover: Ways to Turn Into a Bold Pathfinder

I am publishing a super-low-cost innovation book for €4,99 on Quillmere Open Press to help everyone become a great innovator: young ambitious people without college education nor a big budget. Do you want to help me?

Brief:
Design a book cover 1600 x 2560 pixels for QOP.
Main title: Ways to Turn Into a Bold Pathfinder
Sub title: mindset - insights - skills & tools
Author: Joost ter Brakel
Design: captive, and appealing to everyone
Target Group: young ambitious people without college education

For quillmere please format the height/width ratio of 1.6:1

```html
<!DOCTYPE html>
<html lang="en">
<head>
<meta charset="utf-8">
<title>Ways to Turn Into a Bold Pathfinder — Book Cover</title>
<link href="https://fonts.googleapis.com/css2?family=Montserrat:wght@300;400;700;800&display=swap" rel="stylesheet">
<style>
  :root {
    --sky-top: #3b4255;
    --sky-blue: #5f7190;
    --mid-grey: #8c8b93;
    --floor-light: #b9b7bb;
    --base-dark: #2b2a2f;
    --ink-white: #ffffff;
    --burst-core: #ffd86a;
    --burst-orange: #f36a1e;
    --burst-red: #d8263a;
    --burst-cyan: #3ab4d8;
  }
  html, body {
    margin: 0;
    padding: 0;
    width: 750px;
    height: 1200px;
    overflow: hidden;
    background: var(--base-dark);
  }
  .cover {
    position: relative;
    width: 750px;
    height: 1200px;
    overflow: hidden;
    font-family: "Montserrat", sans-serif;
    color: var(--ink-white);
    background:
      radial-gradient(ellipse 60% 30% at 90% 0%, var(--sky-blue) 0%, transparent 70%),
      linear-gradient(180deg, var(--sky-top) 0%, #666a78 22%, var(--mid-grey) 45%, #9a989d 62%, var(--floor-light) 70%, #5a585d 80%, var(--base-dark) 100%);
  }
  .subtitle {
    position: absolute;
    top: 34px;
    left: 0;
    width: 100%;
    text-align: center;
    font-weight: 300;
    font-size: 25px;
    letter-spacing: 0.5px;
    margin: 0;
  }
  .author {
    position: absolute;
    top: 74px;
    left: 0;
    width: 100%;
    text-align: center;
    font-weight: 800;
    font-size: 45px;
    letter-spacing: 2.5px;
    margin: 0;
  }
  .illustration {
    position: absolute;
    top: 180px;
    left: 0;
    width: 750px;
    height: 790px;
  }
  .title {
    position: absolute;
    top: 960px;
    left: 0;
    width: 100%;
    text-align: center;
    margin: 0;
    font-weight: 800;
  }
  .title-lead {
    display: block;
    font-size: 22px;
    letter-spacing: 3.5px;
    font-weight: 700;
    line-height: 1;
  }
  .title-main {
    display: block;
    font-size: 80px;
    line-height: 0.98;
    letter-spacing: 0;
    margin-top: 12px;
  }
  .title-main.long {
    font-size: 72px;
    margin-top: 2px;
  }
</style>
</head>
<body>
  <main class="cover">
    <p class="subtitle">MINDSET - INSIGHTS - SKILLS &amp; TOOLS</p>
    <p class="author">JOOST TER BRAKEL</p>

    <svg class="illustration" viewBox="0 0 750 790" role="img" aria-label="Glowing light bulb bursting with colourful paint splashes">
      <defs>
        <radialGradient id="burst" cx="50%" cy="52%" r="50%">
          <stop offset="0%" stop-color="var(--burst-core)"/>
          <stop offset="22%" stop-color="var(--burst-orange)"/>
          <stop offset="45%" stop-color="var(--burst-red)"/>
          <stop offset="65%" stop-color="var(--burst-cyan)" stop-opacity="0.75"/>
          <stop offset="100%" stop-color="var(--burst-orange)" stop-opacity="0"/>
        </radialGradient>
      </defs>
      <ellipse cx="375" cy="400" rx="380" ry="380" fill="url(#burst)"/>
    </svg>

    <h1 class="title">
      <span class="title-lead">WAYS TO TURN INTO A</span>
      <span class="title-main">BOLD</span>
      <span class="title-main long">PATHFINDER</span>
    </h1>
  </main>
</body>
</html>
```